FinTech company looking to revamp and expand client-facing interface for our financial models

Pellworth Engines currently has a very simple website that allows clients to interact with our financial models. We are looking to completely redesign the current site and add several extra pages to provide extra functionality. We want the design to have a modern, slick feel, that will work on both a desktop or a tablet. It should be straightforward for clients to move between different pages at any time, and clear from the layout how to interact with the more advanced features. We have included screenshots of existing pages in the attached design brief, as well as sketches of the functionality required by the new pages, but can't provide a direct link to the current site.
Target Market(s)
Professional investors that will be paying to access the interface
Industry/Entity Type
Finance
Number of Pages Required
4 page
Colors
Designer to choose colors to be used in the design.
Look and feel
Each slider illustrates characteristics of the customer's brand and the style your logo design should communicate.

```html
<!DOCTYPE html>
<html lang="en">
<head>
<meta charset="utf-8">
<title>QORVAL – ETF Pairs</title>
<link href="https://fonts.googleapis.com/css2?family=Montserrat:wght@500;600;700&family=Roboto+Condensed:wght@400;500&family=Roboto:wght@400&display=swap" rel="stylesheet">
<style>
:root{
  --page:#e6e6e6;
  --panel:#f4f4f4;
  --white:#ffffff;
  --navy:#0b3470;
  --ink:#111111;
  --black:#1b1b1b;
  --teal:#006b63;
  --grey-btn:#9a9a9a;
  --row-alt:#f1f1f1;
  --muted:#555555;
  --line:#e0e0e0;
}
*{box-sizing:border-box;margin:0;padding:0}
html,body{width:1200px;height:2275px;overflow:hidden}
body{background:var(--page);font-family:'Montserrat',sans-serif;color:var(--ink);position:relative}
.panel{position:absolute;left:14px;top:14px;width:1172px;height:2246px;background:linear-gradient(#f0f0f0,#f7f7f7 20%,#f7f7f7)}
.topbar{position:absolute;left:14px;top:14px;width:1172px;height:55px;background:var(--white);display:flex;box-shadow:0 2px 6px rgba(0,0,0,.06)}
.brand{width:166px;font-weight:700;font-size:18px;line-height:55px;padding-left:53px}
.period{width:83px;text-align:center;font-weight:700;font-size:13px;line-height:55px;border-right:1px solid var(--line)}
.period.active{background:var(--navy);color:var(--white);border:none}
.spacer{flex:1}
.nav-item{display:flex;align-items:center;justify-content:center;gap:8px;font-weight:600;font-size:12.5px;border-left:1px solid var(--line)}
.nav-item svg{width:22px;height:22px}
.tabs{position:absolute;top:106px;left:65px;height:51px;width:1112px}
.tab{position:absolute;bottom:0;height:33px;background:var(--white);font-weight:600;font-size:12.5px;color:#333;text-align:center;line-height:35px;border-radius:3px 3px 0 0}
.tab.tall{height:41px;line-height:41px}
.tab.active{height:51px;line-height:51px;background:var(--black);color:var(--white);border-radius:4px 4px 0 0}
.tab.arrow{line-height:33px}
.tab.add{background:var(--navy);border-radius:3px;height:33px;display:flex;align-items:center;justify-content:center}
.label-btn{position:absolute;left:65px;width:300px;height:37px;border-radius:3px;color:var(--white);font-weight:600;font-size:15.5px;line-height:37px;padding-left:27px}
.label-btn.selected{background:var(--navy);top:194px}
.label-btn.unselected{background:var(--grey-btn);top:549px;padding-left:73px}
.factor-table{position:absolute;left:65px;width:1071px;border-collapse:collapse;background:var(--white);box-shadow:0 1px 4px rgba(0,0,0,.12);border-radius:4px;overflow:hidden}
.factor-table th{height:64px;color:var(--white);font-weight:600;font-size:15.5px;background:var(--teal);width:166px}
.factor-table th.id{background:var(--black);width:406px}
.factor-table td{height:64px;text-align:center;font-family:'Roboto Condensed',sans-serif;font-size:17px;border-left:1px solid var(--line)}
.factor-table td:first-child{border-left:none}
.factor-table tr:nth-child(even) td{background:var(--row-alt)}
.t1{top:245px}.t2{top:600px}
.chart-card{position:absolute;left:65px;top:905px;width:1071px;height:1283px;background:var(--white);border-radius:4px;box-shadow:0 1px 4px rgba(0,0,0,.1)}
.chart-card svg{display:block}
.tick{font-family:'Roboto',sans-serif;font-size:13px;fill:#333}
.tick-sm{font-family:'Roboto',sans-serif;font-size:11.5px;fill:#555}
.legend-title{font-family:'Times New Roman',serif;font-size:12px;fill:#444}
</style>
</head>
<body>
<div class="panel"></div>

<header class="topbar">
  <div class="brand">QORVAL</div>
  <div class="period active">250D</div>
  <div class="period">83D</div>
  <div class="period">42D</div>
  <div class="spacer"></div>
  <div class="nav-item" style="width:130px">
    <svg viewBox="0 0 24 24" fill="none" stroke="#111" stroke-width="2"><path d="M3 11l9-8 9 8M5 10v11h5v-6h4v6h5V10"/></svg>MODELS</div>
  <div class="nav-item" style="width:164px">
    <svg viewBox="0 0 24 24" fill="#111"><circle cx="12" cy="12" r="2.2"/><circle cx="12" cy="4" r="1.5"/><circle cx="12" cy="20" r="1.5"/><circle cx="4" cy="12" r="1.5"/><circle cx="20" cy="12" r="1.5"/><circle cx="6.3" cy="6.3" r="1.5"/><circle cx="17.7" cy="17.7" r="1.5"/><circle cx="17.7" cy="6.3" r="1.5"/><circle cx="6.3" cy="17.7" r="1.5"/></svg>SENSITIVITIES</div>
  <div class="nav-item" style="width:181px">
    <svg viewBox="0 0 24 24" fill="none" stroke="#111" stroke-width="1.8"><path d="M12 2.5l2.9 6.1 6.6.8-4.9 4.6 1.3 6.6L12 17.3l-5.9 3.3 1.3-6.6L2.5 9.4l6.6-.8z"/></svg>FAVOURITES</div>
</header>

<nav class="tabs">
  <div class="tab" style="left:0;width:141px">EQUITIES</div>
  <div class="tab" style="left:147px;width:143px">ETFS</div>
  <div class="tab tall" style="left:295px;width:143px">PAIRS</div>
  <div class="tab active" style="left:443px;width:143px">ETF PAIRS</div>
  <div class="tab tall" style="left:591px;width:143px">FACTORS</div>
  <div class="tab" style="left:739px;width:142px">NEW TAB TITLE #1</div>
  <div class="tab" style="left:886px;width:142px">NEW TAB TITLE #2</div>
  <div class="tab arrow" style="left:1034px;width:36px">
    <svg width="12" height="16" viewBox="0 0 12 16" style="margin-top:9px"><path d="M3 2l6 6-6 6" fill="none" stroke="#777" stroke-width="2.2"/></svg></div>
  <div class="tab add" style="left:1075px;width:37px">
    <svg width="24" height="24" viewBox="0 0 24 24" fill="none" stroke="#fff" stroke-width="1.8"><circle cx="12" cy="12" r="10"/><path d="M12 7v10M7 12h10"/></svg></div>
</nav>

<div class="label-btn selected">Number of Selected Factors : 3</div>
<table class="factor-table t1">
  <tr><th class="id">ID ⌄</th><th>Stat 1</th><th>Stat 2</th><th>Stat 3</th><th>Stat 4</th></tr>
  <tr><td>Factor 1</td><td>-1.4</td><td>0.094</td><td>6.1</td><td>100</td></tr>
  <tr><td>Factor 2</td><td>2.8</td><td>0.085</td><td>3.1</td><td>0.7</td></tr>
  <tr><td>Factor 3</td><td>-3.7</td><td>2.7</td><td>-7.2</td><td>100</td></tr>
</table>

<div class="label-btn unselected">Unselected Factors</div>
<table class="factor-table t2">
  <tr><th class="id">ID ⌄</th><th>Stat 1</th><th>Stat 2</th><th>Stat 3</th><th>Stat 4</th></tr>
  <tr><td>Factor 4</td><td>-1.4</td><td>0.094</td><td>6.1</td><td>100</td></tr>
  <tr><td>Factor 5</td><td>2.8</td><td>0.085</td><td>3.1</td><td>0.7</td></tr>
  <tr><td>Factor 6</td><td>-3.7</td><td>2.7</td><td>-7.2</td><td>100</td></tr>
</table>

<section class="chart-card">
<svg width="1071" height="1283" viewBox="0 0 1160 1390">
  <!-- price chart -->
  <g stroke="#ddd" stroke-width="1">
    <path d="M141 62V350M228 62V350M314 62V350M401 62V350M486 62V350M573 62V350M661 62V350M741 62V350M829 62V350M914 62V350M1002 62V350M1087 62V350"/>
    <path d="M80 132H1095M80 174H1095M80 215H1095M80 256H1095M80 298H1095M80 339H1095" stroke="#eee"/>
  </g>
  <path d="M80 62V350" stroke="#999"/>
  <g class="tick" text-anchor="end">
    <text x="76" y="96">50</text><text x="76" y="137">45</text><text x="76" y="178">40</text><text x="76" y="220">35</text><text x="76" y="261">30</text><text x="76" y="303">25</text><text x="76" y="344">20</text>
  </g>
  <g class="tick" text-anchor="middle">
    <text x="141" y="369">Aug 2018</text><text x="228" y="369">Sep 2018</text><text x="314" y="369">Oct 2018</text><text x="401" y="369">Nov 2018</text><text x="486" y="369">Dec 2018</text><text x="573" y="369">Jan 2019</text><text x="661" y="369">Feb 2019</text><text x="741" y="369">Mar 2019</text><text x="829" y="369">Apr 2019</text><text x="914" y="369">May 2019</text><text x="1002" y="369">Jun 2019</text><text x="1071" y="369">Jul 2019</text>
  </g>
  <polyline fill="none" stroke="#5b9a3c" stroke-width="1.3" points="80,99 95,112 110,165 122,150 130,149 145,154 160,149 172,140 180,132 190,148 200,157 215,146 230,141 245,150 260,149 270,160 280,157 292,150 300,165 315,170 330,182 340,190 350,198 360,186 370,182 385,195 400,198 415,210 430,207 445,222 460,215 470,208 480,215 490,226 500,232 510,244 520,256 535,262 550,273 562,280 575,281 588,270 600,265 612,272 620,265 635,262 650,265 665,258 680,256 690,263 700,265 715,252 730,248 745,258 760,256 775,268 790,265 805,258 820,256 835,262 850,265 865,270 880,273 895,278 910,281 925,292 940,298 955,302 970,306 985,318 1000,323 1015,320 1030,323 1045,320 1060,318 1078,316 1095,314"/>
  <polyline fill="none" stroke="#1d2a80" stroke-width="1.4" points="80,99 95,107 103,120 110,132 118,120 125,116 133,122 140,124 150,118 160,116 170,126 180,132 190,128 200,124 215,133 230,141 245,146 260,149 275,144 290,141 305,146 320,149 330,160 340,174 350,180 360,182 370,172 380,165 390,170 400,174 410,184 420,190 430,175 440,165 450,168 460,174 470,183 480,190 490,194 500,198 510,215 520,232 532,240 545,248 557,244 570,240 585,242 600,240 615,236 630,232 645,236 660,240 675,242 690,240 705,236 720,232 730,225 740,232 750,240 760,248 775,250 790,248 805,252 820,256 835,260 850,265 865,270 880,273 890,278 900,281 915,286 930,289 945,294 960,298 975,302 990,306 1000,311 1010,314 1025,317 1040,318 1055,317 1070,318 1085,318 1095,318"/>

  <!-- spread chart -->
  <g stroke="#ddd">
    <path d="M143 448V735M230 448V735M316 448V735M404 448V735M488 448V735M576 448V735M664 448V735M744 448V735M831 448V735M917 448V735M1004 448V735M1090 448V735"/>
  </g>
  <path d="M80 448V735H1095" stroke="#999" fill="none"/>
  <g class="tick" text-anchor="middle">
    <text x="141" y="443">Aug 2018</text><text x="228" y="443">Sep 2018</text><text x="314" y="443">Oct 2018</text><text x="401" y="443">Nov 2018</text><text x="486" y="443">Dec 2018</text><text x="573" y="443">Jan 2019</text><text x="661" y="443">Feb 2019</text><text x="741" y="443">Mar 2019</text><text x="829" y="443">Apr 2019</text><text x="914" y="443">May 2019</text><text x="1002" y="443">Jun 2019</text><text x="1071" y="443">Jul 2019</text>
    <text x="143" y="754">Aug 2018</text><text x="230" y="754">Sep 2018</text><text x="316" y="754">Oct 2018</text><text x="404" y="754">Nov 2018</text><text x="488" y="754">Dec 2018</text><text x="576" y="754">Jan 2019</text><text x="664" y="754">Feb 2019</text><text x="744" y="754">Mar 2019</text><text x="831" y="754">Apr 2019</text><text x="917" y="754">May 2019</text><text x="1004" y="754">Jun 2019</text><text x="1071" y="754">Jul 2019</text>
  </g>
  <g class="tick" text-anchor="end">
    <text x="76" y="481">30</text><text x="76" y="558">25</text><text x="76" y="636">20</text><text x="76" y="713">15</text>
  </g>
  <polyline fill="none" stroke="#6ea6a0" stroke-width="1.3" points="80,603 100,608 110,662 118,663 125,631 150,628 160,633 167,670 178,670 180,628 195,622 210,617 222,626 230,620 245,615 255,640 270,640 280,643 295,638 305,655 310,680 322,683 335,683 350,678 360,690 375,697 385,713 395,700 402,660 410,630 425,622 430,660 437,678 450,665 460,660 470,650 480,650 490,627 500,625 510,635 525,625 535,590 555,578 560,555 572,550 585,548 588,575 595,548 610,548 618,540 625,530 640,522 650,515 660,505 670,498 680,490 690,520 700,518 710,510 720,512 730,545 740,530 750,520 760,512 770,515 780,510 790,502 800,492 810,478 820,470 830,480 840,480 850,505 860,498 870,490 880,484 890,480 905,474 920,470 930,480 940,485 950,482 960,480 970,475 980,470 990,476 1000,482 1010,480 1020,480 1035,474 1050,468 1060,465 1070,456 1080,450 1092,440"/>

  <!-- factor exposure chart -->
  <path d="M110 815V1018M110 932H1008" stroke="#999" fill="none"/>
  <g class="tick-sm" text-anchor="end">
    <text x="76" y="829">6</text><text x="76" y="864">4</text><text x="76" y="900">2</text><text x="76" y="936">0</text><text x="76" y="971">−2</text><text x="76" y="1006">−4</text>
  </g>
  <g class="tick-sm" text-anchor="middle">
    <text x="107" y="1039">Jul 2018</text><text x="251" y="1039">Sep 2018</text><text x="393" y="1039">Nov 2018</text><text x="534" y="1039">Jan 2019</text><text x="672" y="1039">Mar 2019</text><text x="813" y="1039">May 2019</text><text x="955" y="1039">Jul 2019</text>
  </g>
  <g fill="none" stroke="#111" stroke-width="16" stroke-dasharray="1.6 2.6">
    <polyline points="125,879 160,875 200,872 240,878 280,877 300,868 320,855 340,880 360,885 380,890 400,892 420,888 440,885 460,870 480,865 500,882 520,878 540,880 560,875 590,860 610,852 630,862 660,858 700,855 740,858 760,862 790,868 820,870 850,875 880,878 900,885 930,890 960,888"/>
    <polyline points="125,975 200,974 250,972 300,973 340,970 370,978 400,978 430,976 460,978 500,983 540,985 580,987 610,982 630,995 660,997 700,998 750,996 800,996 850,995 900,996 960,997"/>
  </g>
  <g fill="none" stroke-width="7" stroke-linecap="round" stroke-dasharray="0 6">
    <polyline stroke="#bcbd22" points="125,879 160,875 200,872 240,878 280,877 300,868 320,855 340,880 360,885 380,890 400,892 420,888 440,885 460,870 480,865 500,882 520,878 540,880 560,875 590,860 610,852 630,862 660,858 700,855 740,858 760,862 790,868 820,870 850,875 880,878 900,885 930,890 960,888"/>
    <polyline stroke="#2f6bb0" points="125,975 200,974 250,972 300,973 340,970 370,978 400,978 430,976 460,978 500,983 540,985 580,987 610,982 630,995 660,997 700,998 750,996 800,996 850,995 900,996 960,997"/>
  </g>
  <path d="M936 948v14M932 955h8" stroke="#111" stroke-width="2"/>
  <circle cx="936" cy="955" r="4" fill="#3a9a3a"/>

  <!-- legend -->
  <text class="legend-title" x="1062" y="828">Names</text>
  <g>
    <circle cx="1047" cy="826" r="3" fill="#8ab4d8"/><circle cx="1047" cy="845" r="3" fill="#f5b87a"/><circle cx="1047" cy="863" r="3" fill="#3a9a3a"/><circle cx="1047" cy="882" r="3" fill="#d9626c"/><circle cx="1047" cy="900" r="3" fill="#c4a8d8"/><circle cx="1047" cy="919" r="3" fill="#b09a90"/><circle cx="1047" cy="938" r="3" fill="#f2b5d4"/><circle cx="1047" cy="956" r="3" fill="#bcbcbc"/><circle cx="1047" cy="975" r="3" fill="#bcbd22"/><circle cx="1047" cy="993" r="3" fill="#9ee3e8"/><circle cx="1047" cy="1012" r="3" fill="#2f6bb0"/>
  </g>

  <!-- percentile scatter chart -->
  <path d="M110 1105V1300H1006" stroke="#999" fill="none"/>
  <g class="tick-sm" text-anchor="end">
    <text x="80" y="1117">100</text><text x="80" y="1154">80</text><text x="80" y="1192">60</text><text x="80" y="1229">40</text><text x="80" y="1266">20</text><text x="80" y="1304">0</text>
  </g>
  <g class="tick-sm" text-anchor="middle">
    <text x="112" y="1326">Jul 2018</text><text x="255" y="1326">Sep 2018</text><text x="395" y="1326">Nov 2018</text><text x="536" y="1326">Jan 2019</text><text x="672" y="1326">Mar 2019</text><text x="813" y="1326">May 2019</text><text x="953" y="1326">Jul 2019</text>
  </g>
  <path fill="none" stroke="#bcbd22" stroke-width="7" stroke-linecap="round" stroke-dasharray="0 6" d="M685 1115H960"/>
  <path fill="none" stroke="#bcbd22" stroke-width="7" stroke-linecap="round" d="M135 1113h0M142 1113h0M149 1113h0M156 1113h0M163 1113h0M170 1113h0M177 1113h0M184 1113h0M191 1113h0M198 1113h0M205 1113h0M212 1113h0M220 1116h0M228 1120h0M235 1113h0M245 1118h0M255 1118h0M262 1120h0M330 1113h0M338 1117h0M268 1150h0M280 1175h0M290 1185h0M275 1210h0M300 1205h0M305 1225h0M290 1240h0M310 1175h0M315 1150h0M325 1140h0M330 1120h0M345 1165h0M350 1185h0M355 1200h0M340 1215h0M368 1240h0M375 1270h0M380 1290h0M385 1265h0M395 1258h0M410 1275h0M420 1285h0M430 1250h0M440 1260h0M455 1275h0M462 1190h0M465 1170h0M470 1150h0M470 1113h0M478 1113h0M485 1113h0M492 1113h0M500 1113h0M505 1115h0M505 1295h0M515 1290h0M525 1283h0M535 1278h0M540 1285h0M550 1275h0M560 1282h0M575 1265h0M580 1250h0M585 1240h0M590 1225h0M600 1135h0M605 1140h0M615 1130h0M630 1135h0M640 1125h0M645 1170h0M650 1148h0M655 1130h0M665 1125h0M675 1120h0M680 1115h0M650 1215h0M660 1240h0M635 1260h0M640 1255h0"/>
  <path fill="none" stroke="#2f6bb0" stroke-width="7" stroke-linecap="round" stroke-dasharray="0 6" d="M505 1113H960"/>
  <path fill="none" stroke="#2f6bb0" stroke-width="7" stroke-linecap="round" d="M133 1123h0M140 1118h0M147 1123h0M150 1113h0M133 1185h0M150 1210h0M160 1225h0M165 1245h0M170 1230h0M175 1250h0M180 1240h0M185 1200h0M190 1215h0M195 1220h0M200 1250h0M205 1245h0M210 1250h0M215 1235h0M220 1245h0M225 1240h0M240 1245h0M245 1255h0M250 1250h0M260 1255h0M270 1275h0M280 1282h0M290 1280h0M295 1275h0M300 1278h0M310 1265h0M315 1255h0M320 1250h0M330 1258h0M340 1245h0M345 1262h0M355 1270h0M360 1258h0M375 1280h0M380 1260h0M395 1130h0M400 1120h0M405 1135h0M410 1140h0M415 1125h0M420 1145h0M365 1298h0M375 1298h0M425 1285h0M430 1275h0M440 1265h0M450 1260h0M455 1255h0M460 1240h0M465 1225h0M470 1210h0M475 1200h0M480 1130h0M490 1125h0M500 1118h0"/>
  <path fill="none" stroke="#3a9a3a" stroke-width="7" stroke-linecap="round" d="M928 1297h0M935 1297h0"/>

  <text class="legend-title" x="1062" y="1115">Names</text>
  <g>
    <circle cx="1045" cy="1113" r="3" fill="#8ab4d8"/><circle cx="1045" cy="1132" r="3" fill="#f5b87a"/><circle cx="1045" cy="1150" r="3" fill="#3a9a3a"/><circle cx="1045" cy="1169" r="3" fill="#d9626c"/><circle cx="1045" cy="1187" r="3" fill="#c4a8d8"/><circle cx="1045" cy="1206" r="3" fill="#b09a90"/><circle cx="1045" cy="1224" r="3" fill="#f2b5d4"/><circle cx="1045" cy="1243" r="3" fill="#bcbcbc"/><circle cx="1045" cy="1261" r="3" fill="#bcbd22"/><circle cx="1045" cy="1280" r="3" fill="#9ee3e8"/><circle cx="1045" cy="1298" r="3" fill="#2f6bb0"/>
  </g>
</svg>
</section>
</body>
</html>
```